Tollin Waste Website Design

Our new start-up needs a website design. We plan to help businesses find more sustainable ways to manage their waste. Our initial website aims to gather contact data from potential business customers and comprehensive information from waste facilities and waste transporters. We have a logo design (attached) which we would like included in the website design. I have also attached a number of pages that describe what information should appear on each page as well as a web design brief file that describes the look we are after.

```html
<!DOCTYPE html>
<html lang="en">
<head>
<meta charset="utf-8">
<title>Tollin Waste – Website Design</title>
<link href="https://fonts.googleapis.com/css2?family=Poppins:wght@400;500;600;700&display=swap" rel="stylesheet">
<style>
  :root{
    --green:#6fae1f;
    --green-dark:#4f8a12;
    --green-light:#9ccc3c;
    --ink:#2f2f2f;
    --muted:#666;
    --hero-dark:#2a2b2d;
    --hero-mid:#4a4b4e;
    --page:#ffffff;
  }
  *{box-sizing:border-box;margin:0;padding:0}
  html,body{width:909px;height:1200px;overflow:hidden;background:var(--page);font-family:'Poppins',sans-serif;color:var(--ink)}
  .board{position:relative;width:909px;height:1200px}
  .frame{position:absolute;top:348px;width:432px;height:503px;overflow:hidden}
  .frame--home{left:16px}
  .frame--signup{left:460px}
  .page{position:absolute;top:0;left:0;width:532px;height:620px;transform:scale(0.812);transform-origin:0 0;border:2px solid var(--green);background:#fff;overflow:hidden}

  .header{position:absolute;top:0;left:0;right:0;height:70px;background:#fff}
  .brand{position:absolute;display:flex;align-items:center;gap:7px;white-space:nowrap}
  .header .brand{left:40px;top:22px}
  .brand__dot{width:22px;height:22px;border-radius:50%;background:var(--green);flex:none}
  .brand__name{font-weight:600;font-size:16px;letter-spacing:.3px;color:var(--ink);line-height:1}
  .contact{position:absolute;left:222px;top:13px;display:flex;align-items:center;gap:5px;white-space:nowrap}
  .contact svg{width:16px;height:16px;flex:none}
  .contact__lines{font-size:6px;line-height:9px}
  .contact__phone{font-weight:600;font-size:6.5px}
  .search{position:absolute;left:392px;top:16px;width:95px;height:14px;border:1px solid #ddd;border-radius:8px;font-size:5px;color:#aaa;padding:3px 8px;display:flex;justify-content:space-between;align-items:center}
  .search svg{width:6px;height:6px}
  .nav{position:absolute;left:224px;top:51px;display:flex;gap:15px;font-size:8px;white-space:nowrap}
  .nav a{color:var(--ink);text-decoration:none}
  .nav a.is-active{color:var(--green);font-weight:600}

  .hero{position:absolute;top:70px;left:0;right:0;height:300px;background:radial-gradient(ellipse at 50% 30%,var(--hero-mid),var(--hero-dark) 75%)}
  .hero__content{position:absolute;top:100px;left:0;right:0;text-align:center;color:#fff}
  .hero__title{font-weight:700;font-size:19px;letter-spacing:-.2px}
  .hero__text{font-size:9.5px;line-height:16px;margin-top:6px}
  .btn{display:inline-block;background:var(--green);color:#fff;border-radius:10px;font-size:5.5px;font-weight:600;padding:4px 12px;margin-top:8px}
  .hero__curve{position:absolute;left:0;top:280px;width:532px;height:94px}

  .services{position:absolute;top:392px;left:0;right:0;text-align:center}
  .services__title{color:var(--green-dark);font-weight:700;font-size:15px}
  .cards{position:absolute;top:437px;left:40px;display:flex;gap:16px}
  .card{width:140px;height:126px;background:#fff;border:2px solid #fff;box-shadow:0 1px 4px rgba(0,0,0,.3);position:relative}
  .card__photo{height:102px}
  .card__photo--producers{background:linear-gradient(160deg,#6b6e70,#3e4042)}
  .card__photo--facilities{background:linear-gradient(180deg,#6f9a3c,#c98a2a 60%,#5a5d55)}
  .card__photo--transporters{background:linear-gradient(160deg,#8a9196,#b7b93a 55%,#555c62)}
  .card__label{height:20px;background:var(--green);color:#fff;font-weight:600;font-size:9px;display:flex;align-items:center;justify-content:center;white-space:nowrap}

  .footer{position:absolute;bottom:0;left:0;right:0;height:35px;background:linear-gradient(180deg,var(--green-light),var(--green));color:#fff;font-size:7px;display:flex;align-items:center;justify-content:center}

  .overlay{position:absolute;inset:0;background:rgba(35,35,35,.55)}
  .modal{position:absolute;left:86px;top:115px;width:358px;height:180px;background:#f4f4f4;text-align:center}
  .modal .brand{position:static;justify-content:center;margin-top:28px}
  .modal .brand__name{font-size:22px}
  .modal .brand__dot{width:28px;height:28px}
  .modal__text{font-size:9.5px;font-weight:600;line-height:17px;margin-top:16px}
  .modal__form{margin:10px auto 0;width:252px;height:24px;border:1px solid #bbb;border-radius:12px;background:#fff;display:flex;align-items:center;justify-content:space-between;padding-left:12px;font-size:5.5px;color:#888}
  .modal__btn{background:var(--green);color:#fff;height:22px;width:80px;border-radius:11px;font-size:7.5px;font-weight:600;display:flex;align-items:center;justify-content:center;gap:4px}
  .modal__btn svg{width:8px;height:8px}
  .modal__close{position:absolute;right:2px;top:2px;width:12px;height:12px}
</style>
</head>
<body>
<div class="board">

  <section class="frame frame--home">
    <div class="page">
      <header class="header">
        <div class="brand"><span class="brand__dot"></span><span class="brand__name">TOLLIN WASTE</span></div>
        <div class="contact">
          <svg viewBox="0 0 20 20"><circle cx="10" cy="10" r="9" fill="none" stroke="#6fae1f" stroke-width="1.5"/><path d="M7 5l2 3-1 1c.6 1.4 1.6 2.4 3 3l1-1 3 2-1 2c-4 0-8-4-8-8z" fill="#6fae1f"/></svg>
          <div class="contact__lines"><div class="contact__phone">+1(888) 888 - 8888</div><div>contact@tollinwastemanagement.com</div></div>
        </div>
        <div class="search"><span>Search here</span><svg viewBox="0 0 10 10"><circle cx="4" cy="4" r="3" fill="none" stroke="#888"/><path d="M6.5 6.5L9 9" stroke="#888"/></svg></div>
        <nav class="nav"><a class="is-active">HOME</a><a>About us</a><a>What we do</a><a>Resources</a><a>Contact us</a></nav>
      </header>
      <div class="hero" role="img" aria-label="Pile of black rubbish bags under a stormy sky">
        <div class="hero__content">
          <h1 class="hero__title">WELCOME TO TOLLIN WASTE</h1>
          <p class="hero__text">Sed ut perspiciatis unde omnis iste natus error sit<br>voluptatem accusantium doloremque</p>
          <span class="btn">Read More</span>
        </div>
      </div>
      <svg class="hero__curve" viewBox="0 0 532 94"><path d="M0,22 Q266,118 532,22 L532,94 L0,94Z" fill="#6fae1f"/><path d="M0,30 Q266,130 532,30 L532,94 L0,94Z" fill="#fff"/></svg>
      <div class="services"><h2 class="services__title">TAKE CONTROL OF YOUR WASTE HERE</h2></div>
      <div class="cards">
        <div class="card"><div class="card__photo card__photo--producers" role="img" aria-label="Heap of discarded plastic bottles"></div><div class="card__label">WASTE PRODUCERS</div></div>
        <div class="card"><div class="card__photo card__photo--facilities" role="img" aria-label="Orange refuse truck among trees"></div><div class="card__label">WASTE FACILITIES</div></div>
        <div class="card"><div class="card__photo card__photo--transporters" role="img" aria-label="Worker in hi-vis vest at a sorting plant"></div><div class="card__label">WASTE TRANSPORTERS</div></div>
      </div>
      <footer class="footer">Copyright © 2018. All Rights Reserved.</footer>
    </div>
  </section>

  <section class="frame frame--signup">
    <div class="page">
      <header class="header">
        <div class="brand"><span class="brand__dot"></span><span class="brand__name">TOLLIN WASTE</span></div>
        <div class="contact">
          <svg viewBox="0 0 20 20"><circle cx="10" cy="10" r="9" fill="none" stroke="#6fae1f" stroke-width="1.5"/><path d="M7 5l2 3-1 1c.6 1.4 1.6 2.4 3 3l1-1 3 2-1 2c-4 0-8-4-8-8z" fill="#6fae1f"/></svg>
          <div class="contact__lines"><div class="contact__phone">+1(888) 888 - 8888</div><div>contact@tollinwastemanagement.com</div></div>
        </div>
        <div class="search"><span>Search here</span><svg viewBox="0 0 10 10"><circle cx="4" cy="4" r="3" fill="none" stroke="#888"/><path d="M6.5 6.5L9 9" stroke="#888"/></svg></div>
        <nav class="nav"><a class="is-active">HOME</a><a>About us</a><a>What we do</a><a>Resources</a><a>Contact us</a></nav>
      </header>
      <div class="hero" role="img" aria-label="Pile of black rubbish bags under a stormy sky"></div>
      <svg class="hero__curve" viewBox="0 0 532 94"><path d="M0,22 Q266,118 532,22 L532,94 L0,94Z" fill="#6fae1f"/><path d="M0,30 Q266,130 532,30 L532,94 L0,94Z" fill="#fff"/></svg>
      <div class="services"><h2 class="services__title">TAKE CONTROL OF YOUR WASTE HERE</h2></div>
      <div class="cards">
        <div class="card"><div class="card__photo card__photo--producers" role="img" aria-label="Heap of discarded plastic bottles"></div><div class="card__label">WASTE PRODUCERS</div></div>
        <div class="card"><div class="card__photo card__photo--facilities" role="img" aria-label="Orange refuse truck among trees"></div><div class="card__label">WASTE FACILITIES</div></div>
        <div class="card"><div class="card__photo card__photo--transporters" role="img" aria-label="Worker in hi-vis vest at a sorting plant"></div><div class="card__label">WASTE TRANSPORTERS</div></div>
      </div>
      <footer class="footer">Copyright © 2018. All Rights Reserved.</footer>
      <div class="overlay"></div>
      <div class="modal">
        <svg class="modal__close" viewBox="0 0 12 12"><circle cx="6" cy="6" r="6" fill="#111"/><path d="M4 4l4 4M8 4l-4 4" stroke="#fff" stroke-width="1.3"/></svg>
        <div class="brand"><span class="brand__dot"></span><span class="brand__name">TOLLIN WASTE</span></div>
        <p class="modal__text">Welcome to TOLLIN Waste. We are just getting started. Please<br>register your email address to receive updates from us</p>
        <div class="modal__form"><span>Your email address</span><span class="modal__btn"><svg viewBox="0 0 10 10"><path d="M0 5L10 0 7 10 5 6z" fill="#fff"/></svg>SIGN UP</span></div>
      </div>
    </div>
  </section>

</div>
</body>
</html>
```